Packaging Label Design for Eyelash Extension Adhesive

I need labels designed for my new adhesive I just came out with. This is adhesive for eyelash extensions. I already have my logo and love it and want it incorporated in the label.
This is Medical Grade Very low fume adhesive geared towards sensitive clients but yet so great it can be your regular adhesive for everyone not just your sensitive clients.
The attached files I did myself and I do actually really Love but want it tweaked and more professional lookin and smooth out the lines etc.... it looks grainey and want it crisp and clear. The two design I created are the look and feel for my business.

Target Market(s)

Licensed beauty professionals, certified Lash Artist

Industry/Entity Type

Business

Font styles to use
Sans Serif
Decorative
Script

Colors
6b449b

Requirements
Must have
• My Corva Brow logo, the colors plum and white
• the fonts and look of label to be elegant & stylish
• I love the bracket { } look with ribbon behind it like wrapped around the bottle of adhesvive. which is only 10ml so it is a fairly small bottle
• ***FORGOT TO ADD THAT NEEDS THE LABEL TO EITHER HAVE A FRONT AND BACK 2 SEPERATE STICKERS OR JUST 1 LONG LABEL TO WRAP AROUND THE 10ML BOTTLE, NEED TO ADD INGREDIENTS AND MY BUSINESS INFO ON BACK OF LABEL. IF ONE LABEL IT NEEDS TO BE 1.25"HEIGHT X 3.40" LONG OR 1.25" X 1.5 TWICE

```html
<!DOCTYPE html>
<html lang="en">
<head>
<meta charset="utf-8">
<title>Lumen Sensi Adhesive Label</title>
<link href="https://fonts.googleapis.com/css2?family=Cinzel:wght@400;600&family=Cinzel+Decorative:wght@400&family=Great+Vibes&family=Quicksand:wght@600;700&family=Arimo:wght@400&display=swap" rel="stylesheet">
<style>
  :root {
    --plum-deep: #3d1764;
    --plum: #6b449b;
    --plum-mid: #7a4fb0;
    --plum-light: #a77fd6;
    --lilac-glow: #c9a6ef;
    --ribbon-white: #ffffff;
    --ribbon-silver: #c9c9cf;
    --ink-plum: #4a2380;
    --white: #ffffff;
  }
  html, body {
    margin: 0;
    padding: 0;
    width: 1200px;
    height: 441px;
    overflow: hidden;
    background: var(--plum-deep);
  }
  .label {
    position: relative;
    width: 1200px;
    height: 441px;
    overflow: hidden;
    background:
      radial-gradient(ellipse 260px 180px at 170px 330px, rgba(201,166,239,0.55), transparent 70%),
      radial-gradient(ellipse 300px 200px at 620px 110px, rgba(201,166,239,0.35), transparent 70%),
      radial-gradient(ellipse 200px 260px at 1160px 150px, rgba(201,166,239,0.35), transparent 70%),
      linear-gradient(100deg, var(--plum-deep) 0%, var(--plum) 35%, var(--plum-mid) 55%, var(--plum) 80%, var(--plum-deep) 100%);
  }
  .label-art {
    position: absolute;
    inset: 0;
  }
  .text {
    position: absolute;
    margin: 0;
    white-space: nowrap;
  }
  .front-brand {
    left: 111px; width: 414px; top: 140px;
    text-align: center;
    font-family: "Cinzel Decorative", serif;
    font-size: 24px;
    color: var(--white);
    letter-spacing: 1px;
  }
  .front-tagline {
    left: 111px; width: 414px; top: 186px;
    text-align: center;
    font-family: "Quicksand", sans-serif;
    font-weight: 700;
    font-size: 16.5px;
    color: var(--ink-plum);
  }
  .front-product {
    left: 100px; width: 436px; top: 206px;
    text-align: center;
    font-family: "Cinzel", serif;
    font-size: 47px;
    color: var(--white);
    letter-spacing: 2px;
    text-shadow: 0 1px 2px rgba(61,23,100,0.8), 0 3px 6px rgba(61,23,100,0.4);
  }
  .front-by {
    left: 111px; width: 414px; top: 262px;
    text-align: center;
    font-family: "Great Vibes", cursive;
    font-size: 40px;
    color: var(--white);
  }
  .front-maker {
    left: 111px; width: 414px; top: 300px;
    text-align: center;
    font-family: "Great Vibes", cursive;
    font-size: 42px;
    color: var(--white);
  }
  .back-heading, .back-meta, .back-contact {
    font-family: "Arimo", sans-serif;
    color: var(--white);
    font-size: 16px;
  }
  .back-heading { left: 725px; top: 40px; }
  .back-net { left: 723px; top: 285px; }
  .back-price { right: 116px; top: 285px; }
  .back-contact-title { left: 711px; width: 388px; top: 330px; text-align: center; }
  .back-contact-line { left: 711px; width: 388px; top: 357px; text-align: center; font-size: 17px; }
  .back-product {
    left: 711px; width: 388px; top: 201px;
    text-align: center;
    font-family: "Cinzel", serif;
    font-size: 37px;
    color: var(--plum);
    letter-spacing: 2px;
  }
  .back-tagline {
    left: 711px; width: 388px; top: 242px;
    text-align: center;
    font-family: "Quicksand", sans-serif;
    font-weight: 700;
    font-size: 14px;
    color: var(--ink-plum);
  }
  .back-web {
    left: 711px; width: 388px; top: 389px;
    text-align: center;
    font-family: "Arimo", sans-serif;
    font-size: 16px;
    color: var(--plum-deep);
  }
</style>
</head>
<body>
<main class="label">
  <svg class="label-art" width="1200" height="441" viewBox="0 0 1200 441" aria-hidden="true">
    <defs>
      <linearGradient id="ribbon-sheen" x1="0" y1="0" x2="0" y2="1">
        <stop offset="0" stop-color="#ffffff"/>
        <stop offset="0.55" stop-color="#f4f4f6"/>
        <stop offset="1" stop-color="#c6c6cc"/>
      </linearGradient>
      <radialGradient id="plaque-fill" cx="0.5" cy="0.35" r="0.7">
        <stop offset="0" stop-color="#a77fd6"/>
        <stop offset="0.6" stop-color="#7a4fb0"/>
        <stop offset="1" stop-color="#4e2584"/>
      </radialGradient>
      <radialGradient id="panel-fill" cx="0.45" cy="0.4" r="0.7">
        <stop offset="0" stop-color="#b28ce0"/>
        <stop offset="0.6" stop-color="#7a4fb0"/>
        <stop offset="1" stop-color="#5a2d8f"/>
      </radialGradient>
    </defs>

    <!-- back panel -->
    <rect class="back-panel" x="711" y="28" width="388" height="386" fill="url(#panel-fill)" stroke="#ffffff" stroke-width="2"/>
    <rect class="back-web-strip" x="711" y="385" width="388" height="29" fill="#ffffff"/>

    <!-- wrap ribbon -->
    <rect class="ribbon-edge" x="0" y="182" width="1200" height="80" fill="#4a2380"/>
    <rect class="ribbon" x="0" y="185" width="1200" height="74" fill="url(#ribbon-sheen)"/>
    <rect class="ribbon-inner" x="0" y="191" width="1200" height="62" fill="none" stroke="#d8d8de" stroke-width="1"/>

    <!-- bracket plaque -->
    <path class="plaque-frame"
      d="M318 30 C362 30 396 62 414 94 L476 94 C486 120 506 130 532 133 L532 305 C506 308 486 318 476 344 L414 344 C396 378 362 412 318 412 C274 412 240 378 222 344 L160 344 C150 318 130 308 104 305 L104 133 C130 130 150 120 160 94 L222 94 C240 62 274 30 318 30 Z"
      fill="#ffffff" opacity="0.95"/>
    <path class="plaque"
      d="M318 38 C358 38 390 68 408 100 L470 100 C480 124 500 135 525 138 L525 300 C500 303 480 314 470 338 L408 338 C390 372 358 404 318 404 C278 404 246 372 228 338 L166 338 C156 314 136 303 111 300 L111 138 C136 135 156 124 166 100 L228 100 C246 68 278 38 318 38 Z"
      fill="url(#plaque-fill)"/>
    <rect class="plaque-band" x="111" y="182" width="414" height="80" fill="#ffffff" opacity="0.12"/>
    <line class="brand-rule" x1="205" y1="136" x2="431" y2="136" stroke="#ffffff" stroke-opacity="0.5" stroke-width="1"/>
    <circle class="brand-mark" cx="318" cy="86" r="18" fill="none" stroke="#ffffff" stroke-width="1.5"/>
  </svg>

  <p class="text front-brand">Corva Brow</p>
  <p class="text front-tagline">Certified Medical Grade Lash Adhesive</p>
  <p class="text front-product">LUMEN SENSI</p>
  <p class="text front-by">by</p>
  <p class="text front-maker">Mira Dovell</p>

  <p class="text back-heading">Ingredients :</p>
  <p class="text back-product">LUMEN SENSI</p>
  <p class="text back-tagline">Certified Medical Grade Lash Adhesive</p>
  <p class="text back-meta back-net">Net Wt. : 10 ML</p>
  <p class="text back-meta back-price">MRP : 0.0 $</p>
  <p class="text back-contact back-contact-title">Contact us :</p>
  <p class="text back-contact back-contact-line">000.000.0000 &nbsp;|&nbsp; corvabrow@mail.com</p>
  <p class="text back-web">www.corvabrow.com</p>
</main>
</body>
</html>
```